IT Company needs Website for new Web and Mobile products for Sports and Fitness

Background:

We developed web based white label frontend web solution, backend services and white label mobile apps for to log, analyze, share and control sport and fitness activities. The name of this product suite is "Trevantix" (http://trevantix-example.com)

This products will be used by customers that provide platforms and community systems for sport and fitness. One of the major USP's is, that our technology i open for nearly all common formats, devices and apps out in the market. This means, you can just upload your data directly from device, file or app - e.G. Kestrel, Bolvane, Ravelo, StrideVault, Pacelumo, Zembra and much others.

Two current concrete examples/References

(1) MyQuorel
It's an international platform from quorel for runners. It provides individual training lans and a training log. MyQuorel uses the Backend Product "Trevantix Hub" (see http://hub.trevantix-example.net for a landing page) to integrate device, file and app support. Before this, every user has to track his training with manual inputs

(2) Paceharbor and fen-zine
Both are German customers. Paceharor is focused on runners. fen-zine is focused on Triatheletes. Both use the Product "Trevantix Web". This is a complete web solution with web based frontend solutions for athletes and coaches.

What do we need?
We need website layout for B2B for our products. We don't need lot's of pages. We need the pretty and nice layout, so we can derive the pages we need.

IMPORTANT
We don't talk about the webpages for the product itself (this will be a different project in future). We talk about a website, explaining the products)
Updates

Hi all,

we just start reviewing the first designs, and try to give feedback as detailed as possible. We attached a PDF document, to describe the the products a little bit more detailed. 

As written in the description, in the end we have two different sections. One is the usual stuff like "start page", "about", "contact", "disclaimer", "pricing", "blah...." and one will be the Developer Section, the "Tec Section". This ist aimed to developers (of our customers) that will integrate our products in there existing system or which will integrate our services in there own software.  This "pages" are more like "documentation", so easy to read and cool to look at (cause developers likes it cool, but straight)

Dear all,

we just do the final review. Cause this week is with heavy load, it takes some time...

Cheers

Odell

Target Market(s)

* Platforms and Communities for sport, health and fitness
* Gyms

Industry/Entity Type

Concrete

Font styles to use
Sans Serif

Requirements
Must have
• * Templates shall base on bootstrap. If not, it shall be easily realized on our site with bootstrap or out of the box "full responsive"

* HTML5 / CSS3
Nice to have
• PAGES
- Start Page
- Generic Template (from which we can derive additional pages)
- Contact Page
- Disclaimer Page
- Blog/News Page
- "About us" Page (can be combined with disclaimer)
- One Example product page (in end we have 3 products), shall show (if you need product details, let me know)
- product and it's description
- pricing information
- Add-Ons for the product
- Developer Section Page (Start Point for developers, where the finde "basic technical concepts and developer API's
- Example Developer Page for technical concept
- Example Developer Page for API

LOGO ISSUE
You can use an align to the Logo attached OR provide a new logo. The given logo is a logo for our own B2C Website http://trevantix-example.net. It's not really necessary, that the logo or the color must be used for the product website. Maybe it will be better if it's a complete new one, to avoid irritation between Trevantix as a B2B product and trevantix-example.net as a B2C platform.
Should not have
• No Flash and other proprietary technologies

```html
<!DOCTYPE html>
<html lang="en">
<head>
<meta charset="utf-8">
<title>Trevantix – Our Products</title>
<link rel="stylesheet" href="https://fonts.googleapis.com/css2?family=Source+Sans+3:wght@400;600&family=Fira+Sans+Extra+Condensed:wght@500;600&display=swap">
<style>
:root{
  --orange:#ee7d12;
  --orange-dark:#d9760a;
  --ink:#3a3a3a;
  --text:#2b2b2b;
  --muted:#5a5a5a;
  --navy:#1f2a3a;
  --rule:#d8d8d8;
  --footer:#2b2b2b;
  --white:#ffffff;
}
*{margin:0;padding:0;box-sizing:border-box}
html,body{width:1200px;height:1080px;overflow:hidden;background:var(--white)}
body{position:relative;font-family:"Source Sans 3",Arial,sans-serif;color:var(--text)}
.abs{position:absolute}

/* header */
.brand{left:182px;top:14px}
.brand-name{display:flex;align-items:center;gap:8px;font-size:36px;font-weight:600;color:var(--orange);line-height:1}
.brand-mark{width:14px;height:14px;background:var(--orange)}
.brand-tag{margin-top:12px;font-size:8px;font-weight:600;letter-spacing:.2px;color:#222}
.nav{left:0;top:34px;height:24px;width:1200px}
.nav a{position:absolute;top:5px;transform:translateX(-50%);font-size:10.5px;color:#555;text-decoration:none;text-transform:uppercase;white-space:nowrap}
.nav .sep{position:absolute;top:0;width:1px;height:24px;background:var(--rule)}

/* hero */
.hero{left:0;top:99px;width:1200px;height:262px;background:radial-gradient(ellipse at 15% 20%,#fbe6bf 0%,#f2c27a 30%,#d99046 55%,#b8683a 80%,#8d5a46 100%)}
.hero-photo{left:640px;top:99px;width:560px;height:262px;background:linear-gradient(90deg,rgba(0,0,0,0) 0%,rgba(210,60,55,.35) 40%,rgba(150,90,80,.3) 100%)}
.hero-title{left:182px;top:138px;font-size:31px;font-weight:600;line-height:41px;text-transform:uppercase;letter-spacing:-.3px}
.hero-title .l1{color:var(--orange)}
.hero-title .l2{color:var(--ink)}
.signup{left:180px;top:247px;width:383px;height:39px;background:#f4f4f4;border:1px solid #cfcfcf;border-radius:3px}
.signup span{position:absolute;left:15px;top:12px;font-size:10.5px;color:#888;text-transform:uppercase}
.signup button{position:absolute;right:2px;top:1px;width:133px;height:35px;border:0;border-radius:3px;background:linear-gradient(#f3b332,var(--orange-dark));color:#fff;font:600 16px "Source Sans 3",Arial,sans-serif;text-transform:uppercase}

/* section title */
.section-title{left:213px;top:379px;font-family:"Fira Sans Extra Condensed",Arial,sans-serif;font-size:24px;font-weight:600;color:var(--navy)}
.section-title em{font-style:normal;color:var(--orange)}
.section-shadow{left:214px;top:422px;width:412px;height:10px;background:radial-gradient(ellipse at 50% 0%,rgba(0,0,0,.09),rgba(0,0,0,0) 70%)}

/* product card */
.card{left:206px;top:463px;width:808px;height:477px;border:1px solid #d6d6d6;border-radius:5px;background:#fff;box-shadow:inset 0 0 18px rgba(0,0,0,.08)}
.product-name{left:256px;top:508px;font-size:19px;color:#1c1c1c}
.product-rule{left:256px;top:545px;width:218px;border-top:1px dotted #444}
.feature-title{left:308px;font-size:16px;color:#444}
.feature-list{left:353px;list-style:none}
.feature-list li{display:flex;align-items:center;gap:6px;height:18px;font-size:11px;color:#222}
.feature-list svg{flex:none}

/* footer */
.footer-rule{left:0;top:1003px;width:1200px;border-top:1px dotted #777}
.footer{left:0;top:1006px;width:1200px;height:74px;background:var(--footer)}
.social{left:210px;top:1027px;display:flex;gap:11px}
.social span{width:22px;height:22px;border-radius:2px}
.copyright{right:229px;top:1023px;font-size:11.5px;color:#ddd}
</style>
</head>
<body>

<header>
  <div class="abs brand">
    <div class="brand-name"><span class="brand-mark"></span>Trevantix</div>
    <div class="brand-tag">DIGITAL SPORT AND FITNESS SERVICES</div>
  </div>
  <nav class="abs nav">
    <a href="#" style="left:448px">Home</a>
    <span class="sep" style="left:491px"></span>
    <a href="#" style="left:543px">Trevantix</a>
    <span class="sep" style="left:593px"></span>
    <a href="#" style="left:659px">Fitness Cloud</a>
    <span class="sep" style="left:723px"></span>
    <a href="#" style="left:781px">References</a>
    <span class="sep" style="left:838px"></span>
    <a href="#" style="left:893px">Products</a>
    <span class="sep" style="left:948px"></span>
    <a href="#" style="left:999px">Services</a>
  </nav>
</header>

<section>
  <div class="abs hero" role="img" aria-label="Warm sunset photo of a runner's red running shoes on a track"></div>
  <div class="abs hero-photo"></div>
  <h1 class="abs hero-title"><span class="l1">Die offene Sport- und</span><br><span class="l2">Fitnessplatform fur jeden Sport</span></h1>
  <div class="abs signup"><span>What's your email address :</span><button>Join for free</button></div>
</section>

<main>
  <h2 class="abs section-title">Our <em>Products</em></h2>
  <div class="abs section-shadow"></div>

  <div class="abs card"></div>
  <h3 class="abs product-name">Trevantix Hub</h3>
  <div class="abs product-rule"></div>

  <h4 class="abs feature-title" style="top:576px">Backend Data Services</h4>
  <ul class="abs feature-list" style="top:603px">
    <li><svg width="10" height="10" viewBox="0 0 10 10"><circle cx="5" cy="5" r="5" fill="#ee7d12"/><path d="M4 3l2 2-2 2" stroke="#fff" stroke-width="1.3" fill="none"/></svg>Convert data from several formats and provide in one format via normalized</li>
    <li><svg width="10" height="10" viewBox="0 0 10 10"><circle cx="5" cy="5" r="5" fill="#ee7d12"/><path d="M4 3l2 2-2 2" stroke="#fff" stroke-width="1.3" fill="none"/></svg>JSON format</li>
    <li><svg width="10" height="10" viewBox="0 0 10 10"><circle cx="5" cy="5" r="5" fill="#ee7d12"/><path d="M4 3l2 2-2 2" stroke="#fff" stroke-width="1.3" fill="none"/></svg>Pushing data to several platforms</li>
    <li><svg width="10" height="10" viewBox="0 0 10 10"><circle cx="5" cy="5" r="5" fill="#ee7d12"/><path d="M4 3l2 2-2 2" stroke="#fff" stroke-width="1.3" fill="none"/></svg>Retreiving data from file, device, mail or platforms</li>
    <li><svg width="10" height="10" viewBox="0 0 10 10"><circle cx="5" cy="5" r="5" fill="#ee7d12"/><path d="M4 3l2 2-2 2" stroke="#fff" stroke-width="1.3" fill="none"/></svg>Addtional realtime interface (streaming workouts)</li>
    <li><svg width="10" height="10" viewBox="0 0 10 10"><circle cx="5" cy="5" r="5" fill="#ee7d12"/><path d="M4 3l2 2-2 2" stroke="#fff" stroke-width="1.3" fill="none"/></svg>Export data in several common formats (planned for 2014)</li>
  </ul>

  <h4 class="abs feature-title" style="top:731px">Business Model</h4>
  <ul class="abs feature-list" style="top:758px">
    <li><svg width="10" height="10" viewBox="0 0 10 10"><circle cx="5" cy="5" r="5" fill="#ee7d12"/><path d="M4 3l2 2-2 2" stroke="#fff" stroke-width="1.3" fill="none"/></svg>Data Usage Driven</li>
    <li><svg width="10" height="10" viewBox="0 0 10 10"><circle cx="5" cy="5" r="5" fill="#ee7d12"/><path d="M4 3l2 2-2 2" stroke="#fff" stroke-width="1.3" fill="none"/></svg>Per active user</li>
    <li><svg width="10" height="10" viewBox="0 0 10 10"><circle cx="5" cy="5" r="5" fill="#ee7d12"/><path d="M4 3l2 2-2 2" stroke="#fff" stroke-width="1.3" fill="none"/></svg>Add-Ons as one-time fee</li>
  </ul>

  <h4 class="abs feature-title" style="top:835px">On-Demand or Dedicated</h4>
</main>

<footer>
  <div class="abs footer-rule"></div>
  <div class="abs footer"></div>
  <div class="abs social">
    <span style="background:#3b5b99"></span>
    <span style="background:#3fb4e0"></span>
    <span style="background:#555"></span>
    <span style="background:#f0a030"></span>
    <span style="background:#c8232b"></span>
    <span style="background:#7f9bb0"></span>
  </div>
  <div class="abs copyright">© 2013 trevantix-example.com, All rights reserved</div>
</footer>

</body>
</html>
```